Meridale Bed Company Needs Business Card

Looking for a very nice looking business card. Creative but not extravagant. We sell beds and pillows across the U.S. and need something professional but catchy. I have attached the logo.

Name : Devin Holt
Title : President
Phone : (800) 471-2960
Email: sleep@quilmora.com
Website: www.quilmora.com

Can be single-sided or double-sided
horizontal or vertical

Can use Blues/Greys

Target Market(s)

Mass Market

Industry/Entity Type

Retail

Contact Information for Business Card

Name : Devin Holt
Title : President
Phone : (800) 471-2960
Email: sleep@quilmora.com
Website: www.quilmora.com

Requirements
Must have
• Clean, Modern, Smooth
• Can use Blues/Greys
• On the other side without the information - have something simple like www.quilmora.com or our logo
Nice to have
• Surprise me
Should not have
• Nothing crazy, nothing cluttered

```html
<!DOCTYPE html>
<html lang="en">
<head>
<meta charset="utf-8">
<title>Quilmora Business Card</title>
<link href="https://fonts.googleapis.com/css2?family=Open+Sans:wght@300;400;700&display=swap" rel="stylesheet">
<style>
  :root {
    --brand-blue: #31b4e4;
    --slate: #636267;
    --paper: #ffffff;
    --page: #eeeff1;
  }
  html, body {
    margin: 0;
    width: 1200px;
    height: 1200px;
    overflow: hidden;
    background: var(--page);
    font-family: "Open Sans", Arial, sans-serif;
  }
  .sheet {
    position: relative;
    width: 1200px;
    height: 1200px;
  }
  .card {
    position: absolute;
    left: 180px;
    width: 840px;
    height: 480px;
    border-radius: 18px;
    overflow: hidden;
    box-shadow: 0 6px 22px rgba(0,0,0,0.12);
  }
  /* Back side */
  .card-back {
    top: 90px;
    background: var(--slate);
  }
  .card-back .wordmark {
    position: absolute;
    left: 0;
    right: 0;
    top: 150px;
    text-align: center;
    font-size: 132px;
    font-weight: 300;
    letter-spacing: 2px;
    color: var(--brand-blue);
    line-height: 1;
  }
  .card-back .web-tab {
    position: absolute;
    left: 290px;
    bottom: 0;
    width: 300px;
    height: 58px;
    background: var(--brand-blue);
    border-radius: 10px 10px 0 0;
    color: var(--paper);
    font-size: 17px;
    font-weight: 700;
    letter-spacing: 6px;
    display: flex;
    align-items: center;
    justify-content: center;
  }
  /* Front side */
  .card-front {
    top: 630px;
    background: var(--paper);
  }
  .card-front .wordmark {
    position: absolute;
    left: 190px;
    top: 70px;
    font-size: 116px;
    font-weight: 300;
    letter-spacing: 2px;
    color: var(--brand-blue);
    line-height: 1;
  }
  .name-block {
    position: absolute;
    left: 0;
    top: 268px;
    width: 400px;
    height: 132px;
    background: var(--brand-blue);
    border-radius: 0 8px 8px 0;
    color: var(--paper);
    padding: 30px 0 0 60px;
    box-sizing: border-box;
  }
  .name-block .person {
    margin: 0;
    font-size: 30px;
    font-weight: 700;
    letter-spacing: 0.5px;
    line-height: 1.1;
  }
  .name-block .role {
    margin: 0;
    font-size: 28px;
    font-weight: 700;
    line-height: 1.1;
  }
  .contact-band {
    position: absolute;
    left: 412px;
    top: 200px;
    right: 0;
    height: 150px;
    background: var(--slate);
    border-radius: 8px 0 0 8px;
    color: var(--paper);
    padding: 24px 0 0 44px;
    box-sizing: border-box;
  }
  .contact-list {
    list-style: none;
    margin: 0;
    padding: 0;
  }
  .contact-list li {
    display: flex;
    align-items: center;
    gap: 14px;
    font-size: 21px;
    font-weight: 400;
    line-height: 34px;
  }
  .contact-list svg {
    width: 20px;
    height: 20px;
    flex: none;
  }
</style>
</head>
<body>
<main class="sheet">
  <section class="card card-back" aria-label="Card back">
    <div class="wordmark">quilmora</div>
    <div class="web-tab">www.quilmora.com</div>
  </section>

  <section class="card card-front" aria-label="Card front">
    <div class="wordmark">quilmora</div>

    <div class="name-block">
      <p class="person">DEVIN HOLT</p>
      <p class="role">President</p>
    </div>

    <div class="contact-band">
      <ul class="contact-list">
        <li>
          <svg viewBox="0 0 20 20" aria-hidden="true"><path fill="var(--brand-blue)" d="M3 3c1-1 3-1 4 0l1 3-2 2c1 2 3 4 5 5l2-2 3 1c1 1 1 3 0 4-2 2-6 1-10-3S1 5 3 3z"/></svg>
          (800) 471-2960
        </li>
        <li>
          <svg viewBox="0 0 20 20" aria-hidden="true"><rect x="2" y="5" width="16" height="11" rx="1.5" fill="var(--brand-blue)"/><path d="M2.5 6l7.5 5 7.5-5" fill="none" stroke="var(--slate)" stroke-width="1.5"/></svg>
          sleep@quilmora.com
        </li>
        <li>
          <svg viewBox="0 0 20 20" aria-hidden="true"><g fill="none" stroke="var(--brand-blue)" stroke-width="1.6"><circle cx="10" cy="10" r="8"/><ellipse cx="10" cy="10" rx="3.5" ry="8"/><path d="M2 10h16M3.5 6h13M3.5 14h13"/></g></svg>
          www.quilmora.com
        </li>
      </ul>
    </div>
  </section>
</main>
</body>
</html>
```